Keystone Polished Concrete & Grinding
I'm looking for a business card and logo design for my
new Polished Concrete & Grinding business,
If you were to look up Keystone in the dictionary it would
say, first in importance, order, or position; leading.
Polished Concrete floors are a niche market, that are being used currently in Shopping centres, office spaces and by most high end architects, builders and designers.
i need my business card & logo to stand out from my
competitors, i need my design + logo to reflect this it
needs to be simple, professional, eye catching, easy
to read and scream quality. The logo will need to be
suitable for a whole range of applications including,
uniforms, letter heads, stickers, and eventually
incorporating in vehicle vinyl wrapping.
Target Market(s)
Builders, architects, Interior designers & home owners
Contact Information for Business Card
Front side:
- Keystone Polished Concrete & Grinding.
- Logo
Rear side:
- Liam Varesko
- 0438175092
- info@keystonepcg-example.com.au
- commercial - domestic - industrial
- (later down the line website & space for
social media links
www.keystonepolishedslab-example.com.au)
Colors
Designer to choose colors to be used in the design.
Look and feel
Each slider illustrates characteristics of the customer's brand and the style your logo design should communicate.

```html
<!DOCTYPE html>
<html lang="en">
<head>
<meta charset="utf-8">
<title>Keystone Polished Concrete &amp; Grinding – Business Card</title>
<link href="https://fonts.googleapis.com/css2?family=Roboto:wght@400;500;700&display=swap" rel="stylesheet">
<style>
  :root {
    --brand-blue: #21a5de;
    --ink: #1b1b1b;
    --card-white: #ffffff;
    --stage: #22272b;
    --text-dark: #222222;
  }
  * { box-sizing: border-box; margin: 0; padding: 0; }
  html, body {
    width: 1200px; height: 738px; overflow: hidden;
    background: var(--stage);
    font-family: "Roboto", Arial, sans-serif;
  }
  .canvas {
    position: relative; width: 1200px; height: 738px;
    display: flex; align-items: center; justify-content: center; gap: 40px;
  }
  .card {
    position: relative; width: 540px; height: 309px; overflow: hidden;
    border-radius: 3px;
    box-shadow: 0 10px 30px rgba(0,0,0,.45);
  }

  /* Front */
  .card-front { background: var(--brand-blue); color: var(--card-white); }
  .front-wordmark {
    position: absolute; left: 0; right: 0; top: 126px;
    text-align: center; font-size: 20px; font-weight: 700;
    letter-spacing: .5px; text-transform: uppercase; color: var(--card-white);
  }
  .service-list {
    position: absolute; left: 0; right: 0; bottom: 36px;
    text-align: center; font-size: 14px; letter-spacing: 1px; font-weight: 400;
  }

  /* Back */
  .card-back { background: var(--card-white); }
  .header-band {
    position: absolute; left: 0; top: 0; width: 100%; height: 78px;
    background: var(--brand-blue);
  }
  .header-rule {
    position: absolute; left: 0; top: 78px; width: 100%; height: 5px;
    background: var(--ink);
  }
  .back-wordmark {
    position: absolute; left: 30px; top: 118px; width: 200px;
    display: flex; align-items: center; gap: 10px;
    font-size: 14px; font-weight: 700; line-height: 1.3;
    text-transform: uppercase; color: var(--brand-blue);
  }
  .back-wordmark .dot {
    flex: none; width: 14px; height: 14px; border-radius: 50%; background: var(--brand-blue);
  }
  .holder {
    position: absolute; right: 34px; top: 116px; text-align: right;
  }
  .holder-name {
    font-size: 24px; font-weight: 500; letter-spacing: 1.5px;
    color: var(--brand-blue); text-transform: uppercase;
  }
  .holder-role { font-size: 11px; color: var(--text-dark); margin-top: 14px; }
  .holder-rule {
    position: absolute; right: 100px; top: 152px; width: 190px; height: 1px;
    background: var(--brand-blue);
  }
  .contact-rule {
    position: absolute; left: 30px; top: 226px; width: 280px; height: 1px;
    background: var(--brand-blue);
  }
  .contact-list {
    position: absolute; left: 30px; top: 236px; list-style: none;
    font-size: 12.5px; color: var(--text-dark);
  }
  .contact-list li { display: flex; align-items: center; gap: 8px; height: 19px; }
  .contact-list svg { width: 10px; height: 10px; flex: none; }
</style>
</head>
<body>
<main class="canvas">

  <section class="card card-front" aria-label="Card front">
    <p class="front-wordmark">Keystone Polished Concrete &amp; Grinding</p>
    <p class="service-list">COMMERCIAL - DOMESTIC - INDUSTRIAL</p>
  </section>

  <section class="card card-back" aria-label="Card back">
    <div class="header-band"></div>
    <div class="header-rule"></div>

    <div class="back-wordmark">
      <span class="dot"></span>
      <span>Keystone Polished Concrete &amp; Grinding</span>
    </div>

    <div class="holder">
      <p class="holder-name">Liam Varesko</p>
      <p class="holder-role">Director</p>
    </div>
    <div class="holder-rule"></div>

    <div class="contact-rule"></div>
    <ul class="contact-list">
      <li>
        <svg viewBox="0 0 10 10" aria-hidden="true"><path d="M2 1 L4 3 L3 4 C3.6 5.4 4.6 6.4 6 7 L7 6 L9 8 L8 9 C4.5 9 1 5.5 1 2 Z" fill="var(--brand-blue)"/></svg>
        0438175092
      </li>
      <li>
        <svg viewBox="0 0 10 10" aria-hidden="true"><rect x="1" y="2" width="8" height="6" fill="none" stroke="var(--brand-blue)"/><path d="M1 2 L5 5.5 L9 2" fill="none" stroke="var(--brand-blue)"/></svg>
        info@keystonepcg-example.com.au
      </li>
      <li>
        <svg viewBox="0 0 10 10" aria-hidden="true"><circle cx="5" cy="5" r="4" fill="none" stroke="var(--brand-blue)"/><ellipse cx="5" cy="5" rx="1.8" ry="4" fill="none" stroke="var(--brand-blue)"/><path d="M1 5 H9" stroke="var(--brand-blue)"/></svg>
        www.keystonepolishedslab-example.com.au
      </li>
    </ul>
  </section>

</main>
</body>
</html>
```